Wandering Rooms Stationary Set

Wandering Rooms is a bespoke interior design firm set to provide services to VIP clients with elegance and minimalism is the main theme for our stationary set. We require a full stationary set covering A4 letterhead, A4 & A3 envelopes, business cards, USB's, CDs, email signature and any other item the designer sees fit. logo is already designed and finalized, and we require the designer to use it as is without modifying the logo.

Address to be used on letterhead / business cards ...etc shall be as follows:

Phone : +971 2 518 2047
P.O. Box : 309186
Address: Block C&D, Bldg. 47, Court 12, Abu Dhabi, United Arab Emirates
Website: www.wanderingrooms-example.com

Target Market(s)

VIP Clients

Industry/Entity Type

Interior Design

Font styles to use
Other font styles liked:
• something to be unique

Colors

Designer to choose colors to be used in the design.

Requirements
Must have
• Elegant, minimalistic
Nice to have
• Simple yet elegant design having a sharp yet clean cut format
Should not have
• No additional colours, just colours that are used in the logo (silver, black or gold)

```html
<!DOCTYPE html>
<html lang="en">
<head>
<meta charset="utf-8">
<title>Wandering Rooms — Business Card</title>
<link href="https://fonts.googleapis.com/css2?family=Crimson+Text:wght@400;600&family=Great+Vibes&display=swap" rel="stylesheet">
<style>
  :root {
    --backdrop: #1f1f20;
    --card: #2a2a2b;
    --gold: #b8924f;
    --silver: #c8c8ca;
    --ink-light: #ececec;
    --rule: #8a8a8a;
  }
  * { margin: 0; padding: 0; box-sizing: border-box; }
  html, body {
    width: 1200px; height: 900px; overflow: hidden;
    background: var(--backdrop);
  }
  .sheet {
    width: 1200px; height: 900px;
    display: flex; flex-direction: column; align-items: center; justify-content: center;
    gap: 40px;
  }
  .card {
    position: relative;
    width: 700px; height: 400px;
    background: var(--card);
    border-bottom: 2px solid var(--gold);
    border-left: 1px solid var(--gold);
    box-shadow: 0 14px 30px rgba(0,0,0,.45);
    overflow: hidden;
  }
  .card--front { display: flex; align-items: center; justify-content: center; }
  .wordmark {
    font-family: "Crimson Text", serif;
    font-weight: 400;
    letter-spacing: 0.2em;
    text-transform: uppercase;
    white-space: nowrap;
  }
  .card--front .wordmark { color: var(--silver); font-size: 38px; }

  .card--back { display: flex; align-items: center; }
  .card--back .brand {
    width: 360px; flex: none;
    padding: 0 24px;
    display: flex; justify-content: center;
  }
  .card--back .wordmark { color: var(--gold); font-size: 21px; letter-spacing: 0.18em; }
  .divider {
    width: 1px; height: 230px; flex: none; background: var(--rule);
  }
  .contact {
    padding-left: 30px;
    font-family: "Crimson Text", serif;
    color: var(--ink-light);
  }
  .contact__name {
    font-family: "Great Vibes", cursive;
    color: var(--gold);
    font-size: 34px; line-height: 1;
  }
  .contact__role { font-size: 20px; font-weight: 600; margin-bottom: 16px; }
  .contact__address { font-size: 16px; line-height: 1.35; margin-bottom: 14px; }
  .contact__lines { list-style: none; font-size: 16px; line-height: 1.5; }
  .contact__lines li { display: flex; align-items: center; gap: 10px; }
  .contact__lines svg { width: 14px; height: 14px; flex: none; }
</style>
</head>
<body>
<main class="sheet">
  <section class="card card--front" aria-label="Card front">
    <span class="wordmark">Wandering Rooms</span>
  </section>

  <section class="card card--back" aria-label="Card back">
    <div class="brand"><span class="wordmark">Wandering Rooms</span></div>
    <div class="divider"></div>
    <div class="contact">
      <p class="contact__name">Daniel Harrow</p>
      <p class="contact__role">President</p>
      <p class="contact__address">P.O. Box : 309186,<br>Block C&amp;D, Bldg. 47, Court 12<br>Abu Dhabi, United Arab Emirates</p>
      <ul class="contact__lines">
        <li>
          <svg viewBox="0 0 16 16" aria-hidden="true"><path fill="#b8924f" d="M3.5 1.5l2.5 3-1.4 1.6c.8 1.8 2.1 3.1 3.8 3.9l1.6-1.4 3 2.5-1.3 2.4C6.8 13.3 2.7 9.2 1.1 2.8z"/></svg>
          +971 2 518 2047
        </li>
        <li>
          <svg viewBox="0 0 16 16" aria-hidden="true"><rect x="1" y="3.5" width="14" height="9" fill="#b8924f"/><path d="M1.5 4l6.5 5 6.5-5" stroke="#2a2a2b" stroke-width="1.2" fill="none"/></svg>
          info@wanderingrooms-example.com
        </li>
        <li>
          <svg viewBox="0 0 16 16" aria-hidden="true"><circle cx="8" cy="8" r="6.5" fill="none" stroke="#b8924f" stroke-width="1.4"/><ellipse cx="8" cy="8" rx="2.8" ry="6.5" fill="none" stroke="#b8924f" stroke-width="1.1"/><line x1="1.5" y1="8" x2="14.5" y2="8" stroke="#b8924f" stroke-width="1.1"/></svg>
          www.wanderingrooms-example.com
        </li>
      </ul>
    </div>
  </section>
</main>
</body>
</html>
```